Business Card Design for Marketing Firm

Looking for business card design for higher end marketing firm. Clean but impressionable/trendy. We are a marketing firm that represents manufacturers in the foodservice equipment and supply industry. Our customers are end users such has hotels, restaurants, country clubs, convention centers and casinos as well as distributors of restaurants supplies and equipment, and manufacturers of foodservice equipment and supplies.
Target Market(s)
Hotels, Restaurants, Supply & Equipment Distributors, Foodservice Manufacturers
Industry/Entity Type
Foodservice/Hospitality
Contact Information for Business Card
Name, Title, Contact Number, Email, Website, Social Media, Address
Requirements
Must have
- Clean & Simple but Serious and Impressionable

```html
<!DOCTYPE html>
<html lang="en">
<head>
<meta charset="utf-8">
<title>Meridian Hospitality Reps – Business Card</title>
<link rel="stylesheet" href="https://fonts.googleapis.com/css2?family=Noto+Serif:wght@600&family=Arimo:wght@400&display=swap">
<style>
  :root {
    --navy: #262b6b;
    --navy-ink: #1f2466;
    --paper: #f4f4f4;
    --text-grey: #3a3a3a;
    --white: #ffffff;
    --watermark: rgba(255, 255, 255, 0.06);
    --backdrop: #1b1b1b;
  }
  * { margin: 0; padding: 0; box-sizing: border-box; }
  html, body { width: 1200px; height: 1059px; overflow: hidden; background: var(--backdrop); }
  .stage { position: relative; width: 1200px; height: 1059px; }
  .card { position: absolute; border-radius: 18px; overflow: hidden; }
  .card--front { left: 257px; top: 89px; width: 687px; height: 390px; background: var(--paper); }
  .card--back { left: 254px; top: 547px; width: 693px; height: 393px; background: var(--navy); }
  .serif { font-family: "Noto Serif", Georgia, serif; font-weight: 600; }
  .sans { font-family: "Arimo", Arial, sans-serif; font-weight: 400; }

  .brand-mark { position: absolute; left: 50%; border-radius: 50%; transform: translateX(-50%); }
  .brand-name { position: absolute; left: 0; right: 0; text-align: center; white-space: nowrap; letter-spacing: 0.5px; }

  .front .brand-mark { top: 52px; width: 64px; height: 64px; border: 2px solid var(--navy-ink); }
  .front .brand-name { top: 140px; font-size: 23px; color: var(--navy-ink); }

  .person { position: absolute; right: 368px; top: 229px; text-align: right; }
  .person__name { color: var(--navy-ink); font-size: 24px; line-height: 1.1; white-space: nowrap; }
  .person__title { color: var(--text-grey); font-size: 16px; margin-top: 4px; }
  .divider { position: absolute; left: 342px; top: 216px; width: 1.5px; height: 80px; background: var(--navy-ink); }

  .contacts { position: absolute; left: 365px; top: 207px; list-style: none; }
  .contacts li { display: flex; align-items: center; height: 23.5px; font-size: 16.5px; color: var(--text-grey); white-space: nowrap; }
  .contacts svg { width: 12px; height: 12px; margin-right: 7px; fill: var(--navy-ink); flex: none; }
  .dot { width: 11px; height: 11px; border-radius: 50%; background: var(--navy-ink); margin-right: 7px; flex: none; }

  .address { position: absolute; left: 0; right: 0; top: 334px; text-align: center; font-size: 16px; color: var(--text-grey); }

  .back__watermark { position: absolute; left: 40px; top: -30px; width: 440px; height: 440px; border-radius: 50%; border: 34px solid var(--watermark); }
  .back .brand-mark { top: 112px; width: 92px; height: 92px; border: 3px solid var(--white); }
  .back .brand-name { top: 236px; font-size: 34px; color: var(--white); }
</style>
</head>
<body>
<main class="stage">
  <section class="card card--front front" aria-label="Business card front">
    <div class="brand-mark"></div>
    <div class="brand-name serif">MERIDIAN HOSPITALITY REPS</div>

    <div class="person">
      <div class="person__name serif">DANIEL WHITFORD</div>
      <div class="person__title sans">CEO/Founder</div>
    </div>
    <div class="divider"></div>

    <ul class="contacts sans">
      <li><svg viewBox="0 0 24 24"><path d="M6.6 10.8a15 15 0 0 0 6.6 6.6l2.2-2.2c.3-.3.7-.4 1-.2 1.1.4 2.3.6 3.6.6.6 0 1 .4 1 1V20c0 .6-.4 1-1 1A17 17 0 0 1 3 4c0-.6.4-1 1-1h3.5c.6 0 1 .4 1 1 0 1.3.2 2.5.6 3.6.1.3 0 .7-.2 1z"/></svg>555-014-2290</li>
      <li><svg viewBox="0 0 24 24"><path d="M2 5h20v14H2zm2 2v.5l8 5 8-5V7zm0 2.8V17h16V9.8l-8 5z"/></svg>hello@meridianhospreps.com</li>
      <li><svg viewBox="0 0 24 24"><path d="M12 2a10 10 0 1 0 0 20 10 10 0 0 0 0-20zm0 2c1.2 1.5 2 3.6 2.2 7H9.8C10 7.6 10.8 5.5 12 4zM4.1 13h3.7c.1 2.5.7 4.6 1.6 6.3A8 8 0 0 1 4.1 13zm0-2a8 8 0 0 1 5.3-6.3C8.5 6.4 7.9 8.5 7.8 11zm5.7 2h4.4c-.2 3.4-1 5.5-2.2 7-1.2-1.5-2-3.6-2.2-7zm4.8 6.3c.9-1.7 1.5-3.8 1.6-6.3h3.7a8 8 0 0 1-5.3 6.3zm1.6-8.3c-.1-2.5-.7-4.6-1.6-6.3a8 8 0 0 1 5.3 6.3z"/></svg>www.meridianhospreps.com</li>
      <li><span class="dot"></span>@meridianhospreps</li>
    </ul>

    <div class="address sans">48 Harbor Lane, Suite 210 Lakeview, AB 42180</div>
  </section>

  <section class="card card--back back" aria-label="Business card back">
    <div class="back__watermark"></div>
    <div class="brand-mark"></div>
    <div class="brand-name serif">MERIDIAN HOSPITALITY REPS</div>
  </section>
</main>
</body>
</html>
```